Business cards in digital learning for freelancer

Hello, I need a business cards in french. I work in the Digital learning industries as freeelancer; I'm an expert in digital learning. I work in France. My customer are in the health industry, pharmaceutical industry, and training organization. I've got a logo. I offer three services: consulting, Design, and Training. In the consulting, I offers coaching to choose your digital learning tools and the digital learning strategy. For the Design, I product differents level of elearning like rapid-learning, elearning, micro-learning, video-learning. And for the training service, I've create training about pedagogy, digital learning management project, Digital learning design.
I join my Logo create in this platform. My universe is gamified. I like the life, and I'm very social. I want a card like I'm I. I love Art (painting), Europeen comics. I use in my visual support "permanent maker" font and caracters. I would like cards: elegant, modern, Top class. If you need any information, you can ask me.
thanks for ideas

Target Market(s)

in health industries and training organization for Training manager, instructor, human resources director

Contact Information for Business Card

Phone number : 06 71 38 95 14 , mail: bastiengolmier@quelmoto.fr, web: bastiengolmier.fr , Carrivo

Font styles to use
Sans Serif

Requirements
Must have
• Use my logo and write my 3 services (consulting, training, design)

```html
<!DOCTYPE html>
<html lang="fr">
<head>
<meta charset="utf-8">
<title>Golmier Digital Learning – cartes de visite</title>
<link rel="stylesheet" href="https://fonts.googleapis.com/css2?family=Open+Sans:wght@400;600;700;800&display=swap">
<style>
  :root {
    --orange: #f07427;
    --white: #ffffff;
    --ink: #3c3c3c;
    --rule: #b8b8b8;
    --stage: #1d1d1d;
    --font: "Open Sans", Arial, sans-serif;
  }
  * { box-sizing: border-box; margin: 0; padding: 0; }
  html, body {
    width: 1200px; height: 862px; overflow: hidden;
    background: var(--stage);
    font-family: var(--font);
  }
  .sheet { position: relative; width: 1200px; height: 862px; }

  .card {
    position: absolute;
    width: 580px; height: 375px;
    border-radius: 26px;
    overflow: hidden;
  }
  .card--front { left: 90px; top: 50px; background: var(--orange); color: var(--white); }
  .card--back  { left: 530px; top: 437px; background: var(--white); color: var(--ink); }

  /* brand block */
  .brand { position: absolute; display: flex; flex-direction: column; align-items: center; }
  .brand__row { display: flex; align-items: center; gap: 12px; }
  .brand__dot { border-radius: 50%; flex: none; }
  .brand__name { font-weight: 800; letter-spacing: 2px; line-height: 1; white-space: nowrap; }
  .brand__tag { font-weight: 700; letter-spacing: 3px; text-transform: uppercase; margin-top: 10px; white-space: nowrap; }

  .card--front .brand { left: 0; right: 0; top: 100px; }
  .card--front .brand__dot { width: 40px; height: 40px; background: var(--white); }
  .card--front .brand__name { font-size: 58px; color: var(--white); }
  .card--front .brand__tag { font-size: 14px; color: var(--white); }

  .services {
    position: absolute; left: 0; right: 0; bottom: 62px;
    display: flex; justify-content: center; gap: 34px;
    list-style: none;
    font-size: 22px; font-weight: 600; letter-spacing: 2px;
    white-space: nowrap;
  }
  .services li::before { content: "•"; margin-right: 6px; }

  /* back */
  .card--back .brand { left: 24px; width: 270px; top: 138px; }
  .card--back .brand__dot { width: 26px; height: 26px; background: var(--orange); }
  .card--back .brand__name { font-size: 38px; color: var(--orange); }
  .card--back .brand__tag { font-size: 10px; color: var(--orange); }

  .divider {
    position: absolute; left: 300px; top: 95px;
    width: 1px; height: 180px; background: var(--rule);
  }

  .person { position: absolute; left: 322px; top: 98px; width: 240px; }
  .person__name { font-size: 23px; font-weight: 800; color: var(--orange); letter-spacing: .5px; line-height: 1.1; white-space: nowrap; }
  .person__role { font-size: 16px; color: var(--ink); margin-top: 2px; }

  .contacts { list-style: none; margin-top: 16px; }
  .contacts li { display: flex; align-items: center; gap: 8px; font-size: 14.5px; color: var(--ink); line-height: 1.7; white-space: nowrap; }
  .contacts svg { width: 14px; height: 14px; flex: none; fill: var(--orange); }
</style>
</head>
<body>
<main class="sheet">

  <section class="card card--front" aria-label="Recto">
    <div class="brand">
      <div class="brand__row">
        <span class="brand__dot"></span>
        <span class="brand__name">GOLMIER</span>
      </div>
      <span class="brand__tag">Digital Learning</span>
    </div>
    <ul class="services">
      <li>Consulting</li>
      <li>Training</li>
      <li>Design</li>
    </ul>
  </section>

  <section class="card card--back" aria-label="Verso">
    <div class="brand">
      <div class="brand__row">
        <span class="brand__dot"></span>
        <span class="brand__name">GOLMIER</span>
      </div>
      <span class="brand__tag">Digital Learning</span>
    </div>

    <div class="divider"></div>

    <div class="person">
      <h1 class="person__name">BASTIEN GOLMIER</h1>
      <p class="person__role">Creative Director</p>
      <ul class="contacts">
        <li>
          <svg viewBox="0 0 24 24" aria-hidden="true"><path d="M6.6 10.8a15.1 15.1 0 0 0 6.6 6.6l2.2-2.2c.3-.3.7-.4 1-.2 1.1.4 2.3.6 3.6.6.6 0 1 .4 1 1V20c0 .6-.4 1-1 1A17 17 0 0 1 3 4c0-.6.4-1 1-1h3.5c.6 0 1 .4 1 1 0 1.3.2 2.5.6 3.6.1.3 0 .7-.2 1z"/></svg>
          06 71 38 95 14
        </li>
        <li>
          <svg viewBox="0 0 24 24" aria-hidden="true"><path d="M2 5h20v14H2z M2 5l10 8 10-8" fill="none" stroke="#f07427" stroke-width="2.4" stroke-linejoin="round"/></svg>
          bastiengolmier@example.com
        </li>
        <li>
          <svg viewBox="0 0 24 24" aria-hidden="true"><circle cx="12" cy="12" r="9.5" fill="none" stroke="#f07427" stroke-width="2.4"/><path d="M2.5 12h19M12 2.5c3 3 3 16 0 19M12 2.5c-3 3-3 16 0 19" fill="none" stroke="#f07427" stroke-width="1.8"/></svg>
          www.bastiengolmier.fr
        </li>
        <li>
          <svg viewBox="0 0 24 24" aria-hidden="true"><circle cx="12" cy="12" r="11"/></svg>
          @bastiengolmier
        </li>
      </ul>
    </div>
  </section>

</main>
</body>
</html>
```